Business Card - Tidal Lanes

Need Business Card design for company named Tidal Lanes. Software development focused mainly on Brindle Orvix & Zelt Apps. I've attached our logo with both a black and white background. Please add trademark symbol to logo when using.

```html
<!DOCTYPE html>
<html lang="en">
<head>
<meta charset="utf-8">
<title>Tidal Lanes – Business Card</title>
<link rel="stylesheet" href="https://fonts.googleapis.com/css2?family=Open+Sans:wght@400;700&display=swap">
<style>
  :root {
    --stage: #e9e6e1;
    --card-dark: #050505;
    --ink-light: #ffffff;
    --brand-yellow: #f9c31b;
    --brand-orange: #f59b33;
    --shadow: rgba(0, 0, 0, 0.22);
  }
  * { box-sizing: border-box; margin: 0; padding: 0; }
  html, body {
    width: 1200px;
    height: 720px;
    overflow: hidden;
    background: var(--stage);
    font-family: "Open Sans", Arial, sans-serif;
  }
  .stage {
    width: 1200px;
    height: 720px;
    display: flex;
    align-items: center;
    justify-content: center;
    gap: 40px;
  }
  .card {
    width: 540px;
    height: 309px;
    border-radius: 4px;
    box-shadow: 0 10px 24px var(--shadow);
    color: var(--ink-light);
  }
  .brand {
    display: flex;
    align-items: center;
  }
  .brand__dot {
    border-radius: 50%;
    background: var(--brand-orange);
    flex: none;
  }
  .brand__name {
    font-weight: 700;
    color: var(--ink-light);
    white-space: nowrap;
  }
  .brand__tm {
    font-size: 0.4em;
    vertical-align: super;
    margin-left: 2px;
  }

  /* Front: dark face with contact details */
  .card--front {
    background: var(--card-dark);
    display: flex;
    flex-direction: column;
    align-items: center;
    padding-top: 34px;
  }
  .card--front .brand {
    flex-direction: column;
    gap: 8px;
  }
  .card--front .brand__dot { width: 46px; height: 46px; }
  .card--front .brand__name { font-size: 24px; letter-spacing: -0.5px; }
  .holder {
    margin-top: 22px;
    font-size: 19px;
  }
  .holder__name { font-weight: 700; }
  .holder__title { font-weight: 400; font-size: 15px; }
  .phones {
    margin-top: 8px;
    display: flex;
    align-items: center;
    gap: 10px;
    font-size: 15px;
    letter-spacing: 0.4px;
  }
  .phones__item {
    display: flex;
    align-items: center;
    gap: 6px;
  }
  .phones__icon { width: 14px; height: 16px; fill: var(--ink-light); }
  .address {
    margin-top: 10px;
    font-size: 14px;
    letter-spacing: 0.6px;
  }

  /* Back: orange gradient face with brand name */
  .card--back {
    background: linear-gradient(100deg, var(--brand-yellow) 0%, var(--brand-orange) 100%);
    display: flex;
    align-items: center;
    justify-content: center;
  }
  .card--back .brand { gap: 16px; }
  .card--back .brand__dot {
    width: 40px;
    height: 40px;
    background: var(--ink-light);
  }
  .card--back .brand__name { font-size: 56px; letter-spacing: -1px; }
</style>
</head>
<body>
  <main class="stage">
    <section class="card card--front" aria-label="Business card front">
      <div class="brand">
        <span class="brand__dot"></span>
        <span class="brand__name">Tidal Lanes<span class="brand__tm">™</span></span>
      </div>
      <p class="holder"><span class="holder__name">Your Name,</span> <span class="holder__title">Title</span></p>
      <div class="phones">
        <span class="phones__item">
          <svg class="phones__icon" viewBox="0 0 14 16" aria-hidden="true">
            <rect x="3" y="0" width="8" height="16" rx="1.5"/>
            <rect x="4.5" y="2" width="5" height="7" fill="#050505"/>
          </svg>
          555-214-0187
        </span>
        <span class="phones__item">
          <svg class="phones__icon" viewBox="0 0 16 14" aria-hidden="true">
            <path d="M3 6 L5 2 H11 L13 6 H15 V11 H13 V13 H11 V11 H5 V13 H3 V11 H1 V6 Z"/>
            <rect x="5.5" y="3" width="5" height="3" fill="#050505"/>
          </svg>
          555-214-0392
        </span>
      </div>
      <p class="address">4120 Harbor Row, Marlow, OR 97440</p>
    </section>

    <section class="card card--back" aria-label="Business card back">
      <div class="brand">
        <span class="brand__dot"></span>
        <span class="brand__name">Tidal Lanes<span class="brand__tm">™</span></span>
      </div>
    </section>
  </main>
</body>
</html>
```